Looking for a modern, Professional business card design

We have a simple business card, but are looking for a more modern, professional look. A sample of the basic card is attached as well as the logo. We would also like to add that we offer:
Struggling with your finances?
- Learn to become debt free
- Discover the power of cash
- Control your money instead of it controlling you
Let us help you achieve a new level of financial freedom!
Also, we would like to have a "SPECIAL OFFER!: FREE 30 minute consultation"
Financial Planning

```html
<!DOCTYPE html>
<html lang="en">
<head>
<meta charset="utf-8">
<title>Liberty Money Coaching – Business Card</title>
<link href="https://fonts.googleapis.com/css2?family=Open+Sans:wght@400;600;700;800&display=swap" rel="stylesheet">
<style>
  :root {
    --bg: #e9e6e1;
    --green-dark: #2f8a2a;
    --green-mid: #4fae2c;
    --green-light: #a9d93a;
    --green-text: #3d9a2e;
    --ink: #1d1d1d;
    --grey: #5a5a5a;
    --white: #ffffff;
    --card-shadow: 0 14px 30px rgba(0,0,0,.22);
  }
  * { box-sizing: border-box; margin: 0; padding: 0; }
  html, body { width: 1200px; height: 843px; overflow: hidden; }
  body {
    background: var(--bg);
    font-family: "Open Sans", Arial, sans-serif;
    position: relative;
  }
  .card {
    position: absolute;
    top: 267px;
    width: 540px;
    height: 309px;
    border-radius: 22px;
    box-shadow: var(--card-shadow);
    overflow: hidden;
  }

  /* Back side */
  .card--back {
    left: 40px;
    background: radial-gradient(ellipse 60% 70% at 62% 48%, var(--green-light) 0%, var(--green-mid) 45%, var(--green-dark) 100%);
    color: var(--white);
    text-align: right;
    padding: 26px 30px 0 30px;
  }
  .pitch__heading { font-weight: 800; font-size: 17px; letter-spacing: .3px; text-transform: uppercase; }
  .pitch__list { list-style: none; font-size: 15px; line-height: 1.35; margin-top: 2px; }
  .pitch__list li::after {
    content: ""; display: inline-block; width: 7px; height: 7px; border-radius: 50%;
    background: var(--white); margin-left: 9px; vertical-align: middle;
  }
  .pitch__line { font-size: 15px; line-height: 1.35; }
  .offer__heading { font-weight: 800; font-size: 17px; margin-top: 10px; }
  .offer__detail { font-size: 14px; font-weight: 600; }
  .brand--back { margin-top: 10px; }
  .brand--back .brand__name {
    font-weight: 800; font-size: 38px; line-height: 1; letter-spacing: 1px;
    color: rgba(255,255,255,.88); text-transform: uppercase;
  }
  .brand--back .brand__tagline { font-size: 11px; color: rgba(255,255,255,.85); margin-top: 3px; }

  /* Front side */
  .card--front {
    left: 620px;
    background: linear-gradient(160deg, var(--white) 55%, #eef3ea 100%);
    color: var(--ink);
  }
  .brand--front { position: absolute; left: 34px; top: 40px; }
  .brand__row { display: flex; align-items: center; gap: 12px; }
  .brand__dot { width: 34px; height: 34px; border-radius: 50%; background: var(--green-mid); flex: none; }
  .brand--front .brand__name {
    font-weight: 800; font-size: 30px; line-height: 1; color: var(--ink); text-transform: uppercase; letter-spacing: .5px;
  }
  .brand--front .brand__tagline { font-size: 10.5px; color: var(--grey); margin: 6px 0 0 46px; }
  .contact {
    position: absolute; left: 34px; top: 170px;
    font-size: 15px; line-height: 1.45; color: var(--grey); list-style: none;
  }
  .person { position: absolute; right: 34px; bottom: 34px; text-align: right; }
  .person__name { font-weight: 700; font-size: 21px; color: var(--green-text); }
  .person__title { font-size: 16px; color: var(--ink); }
</style>
</head>
<body>

  <section class="card card--back" aria-label="Card back">
    <p class="pitch__heading">Struggling with your finances?</p>
    <ul class="pitch__list">
      <li>Learn to become debt free</li>
      <li>Discover the power of cash</li>
    </ul>
    <p class="pitch__line">Control your money instead of it controlling you</p>
    <p class="pitch__line">Let us help you achieve a new level of financial freedom!</p>
    <p class="offer__heading">SPECIAL OFFER!</p>
    <p class="offer__detail">FREE 30 minute consultation</p>
    <div class="brand brand--back">
      <p class="brand__name">Liberty Money Coaching</p>
      <p class="brand__tagline">Achieve a new level of personal freedom</p>
    </div>
  </section>

  <section class="card card--front" aria-label="Card front">
    <div class="brand brand--front">
      <div class="brand__row">
        <span class="brand__dot"></span>
        <span class="brand__name">Liberty Money Coaching</span>
      </div>
      <p class="brand__tagline">Achieve a new level of personal freedom</p>
    </div>
    <ul class="contact">
      <li>(205) 555-0182</li>
      <li>daniel@steadymoneypath.com</li>
      <li>www.steadymoneypath.com</li>
    </ul>
    <div class="person">
      <p class="person__name">Daniel R. Hayes</p>
      <p class="person__title">Personal Financial Coach</p>
    </div>
  </section>

</body>
</html>
```